Buch-/eBook-Cover zum Thema Magersucht
Zielgruppe
Ich bin Autorin und suche ein passendes Buchcover. Die Zielgruppe für dieses Buch sind Eltern von magersüchtigen Kindern sowie interessierte medizinische und therapeutische Fachkräfte.
Aufgabenstellung
Bei meinem Buch handelt es sich um einen Ratgeber zur Behandlung von Magersucht bei Kindern und Jugendlichen.
Folgendes muss auf die Vorderseite des Buches:
Titel: Teller trägt Trost
Untertitel: Elterngestützte Begleitung im Alltag
Helga Brunsmeier
Ich wünsche mir ein einfühlsames Cover, das die Schwere der Krankheit spiegelt, aber auch die Hoffnung auf Heilung. Bitte keine plumpen Bilder von Waage, Massband oder dünnen Körpern.
Der Klappentext im Word-Dokument ist für die Rückseite des Buchcovers.

```html
<!DOCTYPE html>
<html lang="de">
<head>
<meta charset="utf-8">
<title>Teller trägt Trost – Buchumschlag</title>
<link href="https://fonts.googleapis.com/css2?family=Roboto:wght@400;700;900&family=Roboto+Condensed:wght@400;500;700&display=swap" rel="stylesheet">
<style>
  :root {
    --back-bg: #f2dcf5;
    --back-circle: #e8c6ef;
    --ink-purple: #6f0c86;
    --spine: #720a8c;
    --front-circle: #a017be;
    --white: #ffffff;
    --photo-light: #efe7dc;
    --photo-mid: #c9a88a;
    --photo-dark: #6e3b2a;
  }
  html, body { margin: 0; padding: 0; overflow: hidden; background: #ffffff; }
  .cover {
    position: relative;
    width: 1200px;
    height: 914px;
    overflow: hidden;
    font-family: "Roboto", sans-serif;
  }
  /* Rückseite */
  .back {
    position: absolute; left: 0; top: 0;
    width: 567px; height: 914px;
    background: var(--back-bg);
    overflow: hidden;
  }
  .back-circle { position: absolute; left: 0; top: 0; }
  .blurb {
    position: absolute; left: 39px; top: 90px; width: 490px;
    color: var(--ink-purple);
  }
  .blurb-title {
    margin: 0 0 6px;
    font-family: "Roboto Condensed", sans-serif;
    font-weight: 700; font-size: 27px; letter-spacing: 0.3px;
  }
  .blurb p {
    margin: 0 0 21px;
    font-size: 14.6px; line-height: 21.6px;
  }
  .blurb strong { font-weight: 700; }
  /* Buchrücken */
  .spine {
    position: absolute; left: 567px; top: 0;
    width: 66px; height: 914px;
    background: var(--spine);
  }
  .spine-text {
    position: absolute; left: 50%; top: 226px;
    transform-origin: left top;
    transform: translateX(-13px) rotate(-90deg) translateX(-498px);
    white-space: nowrap;
    font-family: "Roboto Condensed", sans-serif;
    font-size: 23px; color: var(--white); letter-spacing: 0.5px;
    display: flex; gap: 38px; flex-direction: row-reverse;
  }
  .spine-title { font-weight: 700; }
  .spine-author { font-weight: 400; }
  /* Vorderseite */
  .front {
    position: absolute; left: 633px; top: 0;
    width: 567px; height: 914px; overflow: hidden;
  }
  .front-photo {
    position: absolute; inset: 0;
    background:
      radial-gradient(ellipse at 30% 70%, var(--photo-dark) 0%, transparent 45%),
      radial-gradient(ellipse at 65% 75%, var(--photo-mid) 0%, transparent 50%),
      linear-gradient(180deg, var(--photo-light) 0%, #e4d6c6 55%, #b59277 100%);
  }
  .front-circle { position: absolute; left: 0; top: 0; }
  .front-author {
    position: absolute; left: 0; width: 454px; top: 34px;
    text-align: center;
    font-family: "Roboto Condensed", sans-serif;
    font-size: 24px; color: var(--white); letter-spacing: 0.5px;
  }
  .front-title {
    position: absolute; left: 0; width: 454px; top: 90px; margin: 0;
    text-align: center; color: var(--white);
    font-family: "Roboto", sans-serif; font-weight: 900;
    line-height: 1;
  }
  .front-title .big { display: block; font-size: 80px; letter-spacing: -1px; }
  .front-title .small { display: block; font-size: 44px; margin: 6px 0 8px; }
  .front-subtitle {
    position: absolute; left: 0; width: 454px; top: 332px; margin: 0;
    text-align: center; color: var(--white);
    font-family: "Roboto Condensed", sans-serif; font-weight: 500;
    font-size: 31px; line-height: 40px;
  }
</style>
</head>
<body>
<div class="cover">

  <section class="back">
    <svg class="back-circle" width="567" height="914" aria-hidden="true">
      <circle cx="44" cy="920" r="294" fill="var(--back-circle)"/>
    </svg>
    <div class="blurb">
      <h2 class="blurb-title">TELLER TRÄGT TROST</h2>
      <p>Anorexia Nervosa - Magersucht - ist eine genetisch veranlagte, psychobiologische Krankheit mit einer Sterberate von 10-15%. Je früher die Krankheit diagnostiziert wird, je jünger die Patient:innen bei der Diagnose sind, je rascher mit der Wiederernährung begonnen wird und je schneller ein individuelles gesundes Gewicht erreicht wird, desto grösser ist die langfristige Heilungschance.</p>
      <p>Bei Kindern und Jugendlichen ist gemäß der modernen Anorexie-Forschung die Familie nicht das Problem, sondern in der Regel die größte Ressource für die Heilung. Bei der familienbasierten Pflege zuhause steht die rasche Wiederherstellung des gesunden Gewichts im Vordergrund. Die Eltern übernehmen die volle Verantwortung für die Wiederernährung ihres kranken Kindes, bis sich dessen Verhalten normalisiert hat.</p>
      <p>Dieser Ratgeber liefert ein tiefes Verständnis für die Krankheit auf Basis moderner wissenschaftlicher Erkenntnisse. Er unterstützt Eltern in der Pflege ihrer Kinder zuhause anhand zahlreicher Tipps und erprobter Praxisbeispiele. Von Kochrezepten über den Umgang mit Angst, Aggression und Essensverweigerung bis hin zum Thema Selbstfürsorge ist er eine unentbehrliche Quelle für alle Eltern, die ihre Kinder in die Genesung begleiten möchten. <strong>Anorexie ist heilbar.</strong></p>
    </div>
  </section>

  <section class="spine">
    <div class="spine-text">
      <span class="spine-title">TELLER TRÄGT TROST</span>
      <span class="spine-author">HELGA BRUNSMEIER</span>
    </div>
  </section>

  <section class="front">
    <div class="front-photo" role="img" aria-label="Foto: Mutter und Vater sitzen tröstend neben ihrer Tochter auf einem Sofa und halten ihre Hände, im hellen Wohnzimmer"></div>
    <svg class="front-circle" width="567" height="914" aria-hidden="true">
      <circle cx="259" cy="250" r="256" fill="var(--front-circle)"/>
      <rect x="0" y="0" width="6" height="440" fill="var(--front-circle)"/>
    </svg>
    <div class="front-author">HELGA BRUNSMEIER</div>
    <h1 class="front-title">
      <span class="big">TELLER</span>
      <span class="small">TRÄGT</span>
      <span class="big">TROST</span>
    </h1>
    <p class="front-subtitle">Elterngestützte Begleitung<br>im Alltag</p>
  </section>

</div>
</body>
</html>
```